QVR business card

Need a business card for a company that provides instructional design and elearning development services. The website is here: http://quorvane.studio/

I'm attaching a current logo, as well as the old business card design. While I like to keep it clean, the old design is too simplistic for my liking. The only idea I want to reuse from the old design is placing industry jargon on the back of the card, just need a better way to present it. But if you have other ideas for the back--feel free to experiment.

Please use the colors complementary to the color we have on the website. Thank you!

```html
<!DOCTYPE html>
<html lang="en">
<head>
<meta charset="utf-8">
<title>QVR business card</title>
<link rel="stylesheet" href="https://fonts.googleapis.com/css2?family=Open+Sans:wght@400;600;800&family=PT+Sans+Narrow:wght@400&display=swap">
<style>
  :root {
    --teal: #1db4b0;
    --teal-dark: #169e9a;
    --gold: #d9cb8f;
    --gold-text: #c8b874;
    --ink: #222222;
    --paper: #ffffff;
    --backdrop: #ecebe8;
  }
  * { box-sizing: border-box; margin: 0; padding: 0; }
  html, body { width: 1200px; height: 675px; overflow: hidden; }
  body {
    background: var(--backdrop);
    font-family: "Open Sans", Arial, sans-serif;
    position: relative;
  }
  .card {
    position: absolute;
    top: 188px;
    width: 520px;
    height: 300px;
    overflow: hidden;
    box-shadow: 0 6px 18px rgba(0,0,0,0.18);
  }

  /* Back side */
  .card-back {
    left: 50px;
    background: var(--teal);
    color: var(--paper);
  }
  .help-heading {
    position: absolute;
    left: 10px;
    top: 28px;
    width: 172px;
    text-align: right;
    font-weight: 800;
    font-size: 48px;
    line-height: 1.02;
    letter-spacing: 0.5px;
    text-transform: uppercase;
  }
  .divider {
    position: absolute;
    left: 194px;
    top: 32px;
    width: 2px;
    height: 236px;
    background: var(--paper);
  }
  .jargon-list {
    position: absolute;
    left: 208px;
    top: 30px;
    width: 296px;
    list-style: none;
    font-family: "PT Sans Narrow", "Arial Narrow", sans-serif;
    font-size: 26px;
    line-height: 39px;
    text-transform: uppercase;
    white-space: nowrap;
  }

  /* Front side */
  .card-front {
    left: 630px;
    background: var(--paper);
  }
  .brand {
    position: absolute;
    left: 38px;
    top: 112px;
    display: flex;
    align-items: center;
    gap: 10px;
  }
  .brand-mark {
    width: 22px;
    height: 22px;
    background: var(--teal);
  }
  .brand-name {
    font-weight: 600;
    font-size: 34px;
    color: var(--gold-text);
    letter-spacing: 0.3px;
  }
  .contact {
    position: absolute;
    left: 292px;
    top: 96px;
    color: var(--ink);
  }
  .person-name {
    font-weight: 800;
    font-size: 15px;
    letter-spacing: 0.4px;
    text-transform: uppercase;
  }
  .first-name { color: var(--teal); }
  .last-name { color: var(--gold-text); }
  .person-role {
    font-size: 13px;
    margin-bottom: 12px;
  }
  .contact-list { list-style: none; }
  .contact-item {
    display: flex;
    align-items: center;
    gap: 8px;
    font-size: 14px;
    line-height: 22px;
    white-space: nowrap;
  }
  .contact-icon {
    width: 16px;
    height: 16px;
    flex: none;
    background: var(--teal);
    display: flex;
    align-items: center;
    justify-content: center;
  }
  .contact-icon svg { width: 12px; height: 12px; }
  .front-bands {
    position: absolute;
    left: 0;
    bottom: 0;
  }
</style>
</head>
<body>

<section class="card card-back" aria-label="Card back">
  <h2 class="help-heading">How<br>Can<br>We<br>Help?</h2>
  <div class="divider"></div>
  <ul class="jargon-list">
    <li>Mobile Learning SCORM</li>
    <li>Instructional Design LMS</li>
    <li>MOOCs eLearning HTML5</li>
    <li>Adult Learning Theory</li>
    <li>Gamification Classroom</li>
    <li>xAPI Blended Learning</li>
  </ul>
</section>

<section class="card card-front" aria-label="Card front">
  <div class="brand">
    <span class="brand-mark"></span>
    <span class="brand-name">Quorvane</span>
  </div>

  <div class="contact">
    <p class="person-name"><span class="first-name">Marcus</span> <span class="last-name">Delavine</span></p>
    <p class="person-role">Managing Director</p>
    <ul class="contact-list">
      <li class="contact-item">
        <span class="contact-icon">
          <svg viewBox="0 0 12 12"><path d="M2.5 1h2l1 2.5-1.3 1a6 6 0 0 0 3.3 3.3l1-1.3L11 7.5v2a1 1 0 0 1-1 1A9 9 0 0 1 1.5 2a1 1 0 0 1 1-1z" fill="#fff"/></svg>
        </span>
        555-014-2287
      </li>
      <li class="contact-item">
        <span class="contact-icon">
          <svg viewBox="0 0 12 12"><rect x="1" y="2.5" width="10" height="7" fill="none" stroke="#fff" stroke-width="1.2"/><path d="M1 2.5l5 4 5-4" fill="none" stroke="#fff" stroke-width="1.2"/></svg>
        </span>
        mdelavine@quorvane.studio
      </li>
      <li class="contact-item">
        <span class="contact-icon">
          <svg viewBox="0 0 12 12"><circle cx="6" cy="6" r="4.6" fill="none" stroke="#fff" stroke-width="1.1"/><ellipse cx="6" cy="6" rx="2" ry="4.6" fill="none" stroke="#fff" stroke-width="1"/><path d="M1.4 6h9.2" stroke="#fff" stroke-width="1"/></svg>
        </span>
        www.quorvane.studio
      </li>
    </ul>
  </div>

  <svg class="front-bands" width="520" height="300" viewBox="0 0 520 300" aria-hidden="true">
    <polygon points="0,250 258,250 272,300 0,300" fill="var(--teal)"/>
    <polygon points="266,270 520,270 520,292 272,292" fill="var(--gold)"/>
    <polygon points="272,292 520,292 520,300 274,300" fill="var(--teal)"/>
  </svg>
</section>

</body>
</html>
```